RWT Fittings Ltd Business Cards

We need a business card with our business logo. We provide window and door installations on high-rises in west coast British Colombia, Canada.

I would like my business information and details on one side of the card, and the other side the company name with logo

Target Market(s)

General Contractors

Industry/Entity Type

Construction

Contact Information for Business Card

one side i want my company name and logo in the dark theme logo that i provided

Requirements
Must have
• Marco Peltieri, 16045518293, RWTFittings@mailbox-demo.com, 1407-5194 Linden Row Burnaby BC, V5H 2K9, Owner & Manager

```html
<!DOCTYPE html>
<html lang="en">
<head>
<meta charset="utf-8">
<title>RWT Fittings Ltd – Business Cards</title>
<link rel="stylesheet" href="https://fonts.googleapis.com/css2?family=Roboto:wght@400;500;700&display=swap">
<style>
  :root {
    --stage: #232323;
    --card-white: #ffffff;
    --brand-blue: #26a9e1;
    --tint-blue: #edf5fd;
    --tint-grey: #f3f3f3;
    --text-dark: #1e1e1e;
    --text-grey: #9a9a9a;
    --mark-dark: #1c1c1c;
  }
  * { margin: 0; padding: 0; box-sizing: border-box; }
  html, body {
    width: 1200px; height: 780px; overflow: hidden;
    background: var(--stage);
    font-family: "Roboto", Arial, sans-serif;
  }
  .stage {
    position: relative; width: 1200px; height: 780px;
    display: flex; align-items: center; justify-content: center; gap: 60px;
  }
  .card {
    position: relative; width: 490px; height: 280px; overflow: hidden;
    box-shadow: 0 18px 40px rgba(0,0,0,0.55);
  }

  /* Contact side */
  .card--contact {
    background: linear-gradient(125deg, var(--card-white) 45%, var(--tint-grey) 70%, var(--tint-blue) 100%);
  }
  .brand-lockup {
    position: absolute; left: 28px; top: 30px;
    display: flex; align-items: center; gap: 10px;
  }
  .brand-lockup__square { width: 18px; height: 18px; background: var(--brand-blue); }
  .brand-lockup__name {
    font-size: 20px; font-weight: 700; color: var(--brand-blue); letter-spacing: 0.5px;
  }
  .accent-bar {
    position: absolute; right: 0; top: 150px; width: 14px; height: 62px;
    background: var(--brand-blue);
  }
  .contact-block {
    position: absolute; right: 40px; top: 108px; text-align: left; width: 250px;
  }
  .contact-block__name {
    font-size: 24px; font-weight: 700; line-height: 1.05;
  }
  .contact-block__first { color: var(--brand-blue); }
  .contact-block__last { color: var(--text-grey); }
  .contact-block__role {
    font-size: 12px; font-weight: 700; color: var(--text-dark); margin: 4px 0 10px;
  }
  .contact-block__line {
    font-size: 11.5px; color: var(--text-dark); line-height: 1.4;
    display: flex; align-items: center; gap: 6px;
  }
  .contact-block__line svg { flex: none; }
  .contact-block__gap { height: 6px; }

  /* Brand side */
  .card--brand {
    background: var(--brand-blue);
    display: flex; align-items: center; justify-content: center;
  }
  .brand-mark {
    display: flex; align-items: center; gap: 14px;
  }
  .brand-mark__square { width: 30px; height: 30px; background: var(--mark-dark); }
  .brand-mark__name {
    font-size: 34px; font-weight: 700; color: var(--mark-dark); letter-spacing: 0.5px;
  }
</style>
</head>
<body>
<main class="stage">
  <section class="card card--contact" aria-label="Contact side">
    <div class="brand-lockup">
      <span class="brand-lockup__square"></span>
      <span class="brand-lockup__name">RWT Fittings Ltd</span>
    </div>
    <div class="accent-bar"></div>
    <div class="contact-block">
      <h1 class="contact-block__name">
        <span class="contact-block__first">Marco</span>
        <span class="contact-block__last">Peltieri</span>
      </h1>
      <p class="contact-block__role">Owner &amp; Manager</p>
      <p class="contact-block__line">1407-5194 Linden Row</p>
      <p class="contact-block__line">Burnaby BC, V5H 2K9</p>
      <div class="contact-block__gap"></div>
      <p class="contact-block__line">
        <svg width="12" height="12" viewBox="0 0 24 24" aria-hidden="true"><path fill="#26a9e1" d="M6.6 10.8a15 15 0 0 0 6.6 6.6l2.2-2.2a1 1 0 0 1 1-.25 11.4 11.4 0 0 0 3.6.57 1 1 0 0 1 1 1V20a1 1 0 0 1-1 1A17 17 0 0 1 3 4a1 1 0 0 1 1-1h3.5a1 1 0 0 1 1 1c0 1.25.2 2.45.57 3.6a1 1 0 0 1-.25 1z"/></svg>
        1 604 551 8293
      </p>
      <p class="contact-block__line">
        <svg width="12" height="12" viewBox="0 0 24 24" aria-hidden="true"><rect x="2" y="5" width="20" height="14" rx="2" fill="#26a9e1"/><path d="M3 6l9 7 9-7" fill="none" stroke="#fff" stroke-width="2"/></svg>
        RWTFittings@mailbox-demo.com
      </p>
    </div>
  </section>

  <section class="card card--brand" aria-label="Brand side">
    <div class="brand-mark">
      <span class="brand-mark__square"></span>
      <span class="brand-mark__name">RWT Fittings Ltd</span>
    </div>
  </section>
</main>
</body>
</html>
```